Brand and Marketing Coach Needs PDF Designed

I have content that i need placed into a simple but great PDF design. The PDF is about the formula I use to build personal brands. This is geared towards entrepreneurs, experts, coaches, therapists, wellness practitioners, and indpendent business owners who serve to improve the lives of others.
The company name is changing from TorvelCast to Selling with the Village (I don't have that logo yet, so working backwards a bit. For now, the TorvelCast logo can be used.) My brand is NOT formal and corporate, but it's also not neon-pink and screaming at you. It's down to earth, hip, a bit modern but warm. It's about no BS and authenticity. The final deliverable should make the reader feel focused, smart, motivated and hopeful.

Target Market(s)

Conscious entrepreneurs and small business owners. this one is specifically for pharmacy entrepreneurs but this will be used for various audiences later.

Font styles to use
Sans Serif

Colors
eaf1f7
3377b5
6b449b
f37122
faa54b
f68e4e
ffc214

Requirements
Must have
• Modern design. colors that match logo - 4e5583 (i think that is the blue.) d65a40.
• Could have these colors as well: c6a254, 01bcc3
• But open to other colors
Nice to have
• I'd like to see some ways to make this PDF simple and readable, and eye-catching. I'd also like to use the uploaded ebooks for design ideas.
Should not have
• neon colors, clip art

```html
<!DOCTYPE html>
<html lang="en">
<head>
<meta charset="utf-8">
<title>The Personal Brand Formula – For Pharmacy Entrepreneurs</title>
<link href="https://fonts.googleapis.com/css2?family=Oswald:wght@300;400;500&family=Tinos:ital,wght@0,400;0,700;1,400&family=Open+Sans:wght@600;700&family=Homemade+Apple&display=swap" rel="stylesheet">
<style>
  :root {
    --navy: #4e5583;
    --gold: #c6a254;
    --gold-line: #e6d7ae;
    --mist: #b6c3d3;
    --ink: #1e1e22;
    --orange: #f07c3a;
    --orange-soft: #f6a673;
    --blue: #4a8fc6;
    --blue-soft: #9cc3e3;
    --paper: #ffffff;
    --portrait-a: #efe3c4;
    --portrait-b: #d9d5cf;
    --bg-top: #dcc3e0;
    --bg-bottom: #c07aa8;
  }
  * { box-sizing: border-box; margin: 0; padding: 0; }
  html, body { width: 794px; height: 1200px; overflow: hidden; }
  body {
    position: relative;
    background: linear-gradient(180deg, var(--bg-top) 0%, var(--bg-bottom) 100%);
    font-family: "Tinos", "Times New Roman", serif;
    color: var(--ink);
  }
  .page {
    position: absolute;
    width: 358px; height: 277px;
    background: var(--paper);
    overflow: hidden;
  }
  .col-l { left: 34px; } .col-r { left: 406px; }
  .row-1 { top: 27px; } .row-2 { top: 318px; } .row-3 { top: 611px; } .row-4 { top: 902px; }

  .band {
    height: 40px; background: var(--navy);
    color: #fff; font-style: italic; font-weight: 700;
    font-size: 7.6px; padding: 0 26px; display: flex; align-items: center;
  }
  .band.thin { height: 13px; }
  .content { padding: 14px 16px 0 26px; }
  .content p { font-size: 6.7px; line-height: 1.4; margin-bottom: 7px; }
  h2 {
    font-family: "Oswald", sans-serif; font-weight: 400;
    font-size: 21px; line-height: 1.05; color: var(--ink);
    letter-spacing: -0.2px; margin-bottom: 8px;
  }
  h2.small { font-size: 17px; }

  /* cover */
  .cover-top { height: 119px; background: var(--navy); position: relative; }
  .cover-frame {
    position: absolute; left: 48px; top: 14px; width: 262px; height: 92px;
    border: 2px solid var(--gold);
    display: flex; flex-direction: column; align-items: center; justify-content: center;
    font-family: "Oswald", sans-serif; color: var(--gold); line-height: 1;
  }
  .cover-frame .t1 { font-size: 38px; font-weight: 400; letter-spacing: 0.5px; }
  .cover-frame .t2 { font-size: 28px; font-weight: 300; letter-spacing: 3.5px; margin-top: 2px; }
  .cover-sub { height: 37px; background: var(--mist); text-align: center; padding-top: 5px; }
  .cover-sub .aud { font-family: "Open Sans", sans-serif; font-weight: 600; color: var(--navy); font-size: 12px; }
  .cover-sub .tag { font-style: italic; font-size: 6.8px; margin-top: 1px; }
  .cover-photo {
    position: absolute; left: 0; top: 156px; width: 300px; height: 121px;
    background: linear-gradient(90deg, #3c3c3c 0%, #7d7d7d 35%, #d6d6d6 70%, rgba(255,255,255,0) 100%);
  }
  .cover-script {
    position: absolute; right: 20px; top: 180px; width: 220px;
    font-family: "Homemade Apple", cursive; color: var(--navy);
    font-size: 10.5px; line-height: 2; text-align: right;
  }
  .cover-logo {
    position: absolute; right: 66px; bottom: 18px;
    display: flex; align-items: center; gap: 4px;
    font-family: "Open Sans", sans-serif; font-weight: 700; font-size: 12px; color: var(--navy);
  }
  .cover-logo .dot { width: 11px; height: 11px; border-radius: 50%; background: var(--gold); }

  /* branding table */
  .compare { display: flex; margin: 4px 0 6px; }
  .compare .cell { width: 50%; }
  .compare .head {
    font-family: "Open Sans", sans-serif; font-weight: 700; font-size: 10.5px;
    text-align: center; padding: 3px 0;
  }
  .compare .body {
    color: #fff; font-weight: 700; font-size: 6.6px; line-height: 1.35;
    padding: 4px 6px 6px; height: 49px;
  }
  .is-not .head { background: var(--orange-soft); color: #b7481e; }
  .is-not .body { background: var(--orange); }
  .is .head { background: var(--blue-soft); color: #1f4f82; }
  .is .body { background: var(--blue); }

  .quote { position: relative; height: 76px; }
  .quote-portrait {
    position: absolute; left: 12px; top: 4px; width: 72px; height: 70px;
    background: linear-gradient(135deg, var(--portrait-a), var(--portrait-b));
  }
  .quote-card {
    position: absolute; left: 84px; top: 18px; width: 226px; height: 50px;
    border: 1px solid var(--gold-line); border-radius: 10px; background: #fff;
    padding: 8px 38px 0 10px; text-align: center;
  }
  .quote-card q { display: block; font-style: italic; font-weight: 700; font-size: 7.4px; line-height: 1.3; quotes: "“" "”"; }
  .quote-card .who { font-size: 6px; color: #b08a3a; margin-top: 4px; }
  .quote-mark {
    position: absolute; right: 7px; top: 11px; width: 26px; height: 26px;
    border-radius: 50%; border: 1px solid var(--gold);
    color: var(--gold); font-family: "Oswald", sans-serif; font-size: 20px;
    display: flex; align-items: center; justify-content: center; line-height: 1; padding-top: 7px;
  }

  .pillars {
    font-family: "Oswald", sans-serif; color: var(--navy); font-weight: 400;
    font-size: 20px; line-height: 1.22; text-align: center; margin: 6px 0 10px;
  }
</style>
</head>
<body>

  <section class="page col-l row-1 cover">
    <div class="cover-top">
      <div class="cover-frame">
        <span class="t1">THE PERSONAL</span>
        <span class="t2">BRAND FORMULA</span>
      </div>
    </div>
    <div class="cover-sub">
      <div class="aud">For Pharmacy Entrepreneurs</div>
      <div class="tag">The quick n’ dirty guide to creating a unique personal brand that attracts your ideal clients.</div>
    </div>
    <div class="cover-photo" role="img" aria-label="Black and white photo of the brand coach seated outdoors"></div>
    <div class="cover-script">Step it up, get noticed, and<br>grow your client base.</div>
    <div class="cover-logo"><span class="dot"></span>TorvelCast</div>
  </section>

  <section class="page col-r row-1">
    <div class="band">I’m so glad you’re here! Before we start, a few things:</div>
    <div class="content">
      <h2>WHAT THIS IS</h2>
      <p><strong>The Personal Brand Formula</strong> consists of the exact steps I take to create unique and authentic brands for my clients. It is also what will drive your entire marketing strategy.</p>
      <p><em>One mistake I see entrepreneurs make is to consider BRAND as a separate entity from MARKETING. These two essential elements of your business are deeply connected.</em></p>
      <p>Rather than giving you the elements of a brand, which is really the end product of this work – what I’m giving you here are the essential building blocks, designed to help you discover and unleash your unique brand.</p>
      <p>This is what most people don’t tell you about because it’s the deep work that happens in the background.</p>
      <p><em>When you go through the steps to create your own brand, not only do you build a brand that attracts your ideal clients, but your marketing falls into place, and you finally learn what makes you stand way above the competition.</em></p>
      <p>Yes, it’s true. When you take the time to create your brand, your messaging and marketing strategy fall into place. And this formula is what gets you there.</p>
    </div>
  </section>

  <section class="page col-l row-2">
    <div class="band"></div>
    <div class="content">
      <h2>WHO THIS IS FOR</h2>
      <p><strong>The Personal Brand Formula</strong> is for you if you’re a pharmacy entrepreneur who is starting or already running a business or practice. You may be moving a brick and mortar business online; creating a new business as a coach, patient advocate or navigator; or developing a service that will help your peers or patients.</p>
      <p>If you already have a business, you feel frustrated because you’re not attracting your ideal clients – the type of clients you know you’re meant to serve. And you don’t know how you’ll continue to expand your business.</p>
      <p>If you’re in start-up, you understand that now is the time to nail down the right brand image and messaging so you can come out of the gate running, rather than wasting your precious time and money on tactics that don’t work.</p>
    </div>
  </section>

  <section class="page col-r row-2">
    <div class="band">Long story short, you’re ready to step it up, get noticed, and grow your client base.</div>
    <div class="content">
      <h2>1. START HERE</h2>
      <p>Freedom, impact, and profit… one or all of these are the reasons you started, or want to start, a business…</p>
      <p>But right now, you’re wondering how you’re going to stand out from all the online noise.</p>
      <p>Chatterly is supersaturated with experts and businesses offering very similar if not exactly the same things you do, which makes you doubt how doable and realistic this business thing really is.</p>
      <p>Naturally, when faced with this, you rush to create a logo, a website, and a presence on social media. And this is when I start to worry.</p>
      <p>Because that is COMPLETELY BACKWARDS!</p>
      <p>It’s similar to a doctor prescribing medications to treat a patient’s symptoms without identifying and understanding what is causing them. The symptoms could be side effects of another medicine, the results of illness, or could stem from any number of issues.</p>
    </div>
  </section>

  <section class="page col-l row-3">
    <div class="band"></div>
    <div class="content" style="padding-top:18px">
      <p>Writing your website copy without knowing how to stand apart from others in your industry, position yourself as the expert, or the exact words and phrases that will get your ideal client’s attention is a big waste of your time and money.</p>
      <p>When I see business owners do this, their eBook doesn’t perform as they expected, their website is dead in the water, and they can’t seem to get the right clients.</p>
      <p>What I do for my clients, before I can even begin thinking about their marketing, is to DEFINE them… figure out who they are, what they’re about, and how to differentiate them so they’ll stand out from all the online noise.</p>
      <p>This is the way to build a strong and authentic brand.</p>
    </div>
  </section>

  <section class="page col-r row-3">
    <div class="band thin"></div>
    <div class="content" style="padding-top:12px">
      <h2 class="small">2. QUICK N’ DIRTY -<br>WHAT BRANDING IS AND IS NOT</h2>
      <div class="compare">
        <div class="cell is-not">
          <div class="head">BRANDING IS NOT</div>
          <div class="body">Branding is NOT your logo, colors, and fonts. That is visual branding, and you cannot create that until you have defined your brand.</div>
        </div>
        <div class="cell is">
          <div class="head">BRANDING IS</div>
          <div class="body">Branding is how you make someone feel after they’ve heard you talk, read your blog post, visited your website…</div>
        </div>
      </div>
      <p>Your brand has an essence, a personality, a definitive way of communicating. Your brand tells your story, speaks to your ideal client in a language they understand and causes them to have an emotional reaction.</p>
      <div class="quote">
        <div class="quote-portrait" role="img" aria-label="Portrait of the quoted founder"></div>
        <div class="quote-card">
          <q>Your brand is what other people say about you when you’re not in the room.</q>
          <div class="who">Dana Whitlock, the founder of Northmark.co</div>
          <span class="quote-mark">”</span>
        </div>
      </div>
    </div>
  </section>

  <section class="page col-l row-4">
    <div class="band"></div>
    <div class="content" style="padding-top:14px">
      <p>When people know and trust your brand, they become clients. To have a credible and influential personal brand, you need to be able to articulate three things:</p>
      <div class="pillars">WHO YOU ARE<br>WHAT YOU DO<br>HOW YOU DO IT</div>
      <p>Your personal brand will define how you present yourself on all your marketing platforms – on and offline. It’s everything you and your team say and do. It’s what you blog about, how you write, the photos you share. It’s the message that comes through loud and clear every time, even when no words are uttered.</p>
      <p>Without a brand, you fade into online oblivion.</p>
      <p>This is your foundation and the BLUEPRINT for all you do.</p>
    </div>
  </section>

  <section class="page col-r row-4">
    <div class="band"></div>
    <div class="content" style="padding-top:22px">
      <h2 class="small">3. FOLLOW THE PERSONAL BRAND FORMULA</h2>
      <p>to be continue</p>
    </div>
  </section>

</body>
</html>
```